New Business Card Design Project

We require a business card design for Vexalund, a newly established Indian company.
Our focus is on the development, manufacturing, and export of a diverse array of pharmaceutical products on a global scale. The card should convey a professional appearance, as our primary markets are in Africa, China, and Southeast Asian nations.
We envision a two-sided business card, with the reverse side dedicated to a logo set against a solid color or an elegantly designed pattern. The corners should be rounded. We would appreciate seeing both horizontal and vertical design options. We trust the designer to utilize their expertise in creating this design.

The content for the business card is included in the attached Word file.

Target Market(s)

Our primary markets are in Africa, China, and Southeast Asian, Latin America, Maldives, Sri Lanka

Industry/Entity Type

Pharmaceutical Manufacturing and Export

Contact Information for Business Card

Colors

Designer to choose colors to be used in the design.

Requirements
Must have
• The reverse side of the business card features solely the logo along with the tagline, "Care Beyond Borders."
Should not have
• The logo should not exceed two instances, encompassing both the front and back sides of the card.

```html
<!DOCTYPE html>
<html lang="en">
<head>
<meta charset="utf-8">
<title>Vexalund Business Card</title>
<link href="https://fonts.googleapis.com/css2?family=Montserrat:wght@400;500;700&display=swap" rel="stylesheet">
<style>
  :root {
    --stage: #2b2c2e;
    --card-white: #ffffff;
    --card-white-shade: #f1f1f1;
    --brand-blue: #1f9ad6;
    --brand-coral: #e8594a;
    --coral-light: #f3a395;
    --rule-coral: #f0a093;
    --ink: #2f2f33;
  }
  * { box-sizing: border-box; margin: 0; padding: 0; }
  html, body {
    width: 1200px; height: 900px; overflow: hidden;
    background: var(--stage);
    font-family: "Montserrat", sans-serif;
  }
  .stage {
    position: relative; width: 1200px; height: 900px;
    display: flex; justify-content: center; align-items: center; gap: 100px;
  }
  .card {
    position: relative; width: 360px; height: 630px;
    border-radius: 36px; overflow: hidden;
  }
  .card-front {
    background: linear-gradient(160deg, var(--card-white) 0%, var(--card-white-shade) 100%);
    color: var(--ink);
  }
  .brand {
    position: absolute; top: 120px; left: 0; right: 0;
    display: flex; justify-content: center; align-items: center; gap: 12px;
  }
  .brand-dot {
    width: 22px; height: 22px; border-radius: 50%;
    background: var(--brand-coral);
  }
  .brand-name {
    font-weight: 700; font-size: 46px; color: var(--brand-blue);
    letter-spacing: 0.5px;
  }
  .details {
    position: absolute; left: 38px; right: 30px; top: 330px;
  }
  .person-name {
    font-weight: 700; font-size: 21px; color: var(--brand-blue);
    letter-spacing: 0.5px;
  }
  .person-role { font-size: 16px; margin-top: 4px; }
  .rule { height: 1.5px; background: var(--rule-coral); margin: 14px 0; }
  .address { font-size: 15.5px; line-height: 1.35; }
  .contact-list { list-style: none; font-size: 15.5px; line-height: 1.4; }
  .contact-list li { display: flex; align-items: center; gap: 10px; }
  .contact-list svg { width: 16px; height: 16px; flex: none; }
  .tagline-front {
    font-size: 23px; font-weight: 500; color: var(--brand-blue);
    letter-spacing: 1px; margin-top: 6px; white-space: nowrap;
  }
  .card-back {
    background: var(--brand-coral);
  }
  .back-pattern {
    position: absolute; inset: 0;
    background: linear-gradient(160deg, var(--coral-light) 0%, var(--brand-coral) 55%, #e55443 100%);
  }
  .back-brand {
    position: absolute; left: 0; right: 0; bottom: 90px;
    text-align: center; color: var(--card-white);
  }
  .back-name { font-weight: 700; font-size: 34px; letter-spacing: 0.5px; }
  .back-rule { height: 1.5px; background: rgba(255,255,255,0.7); margin: 16px 40px; }
  .back-tagline { font-weight: 700; font-size: 19px; letter-spacing: 1px; white-space: nowrap; }
</style>
</head>
<body>
<main class="stage">
  <section class="card card-front" aria-label="Front of card">
    <div class="brand">
      <span class="brand-dot"></span>
      <span class="brand-name">Vexalund</span>
    </div>
    <div class="details">
      <h1 class="person-name">ARJUN K. MALVADE</h1>
      <p class="person-role">CEO Of Vexalund</p>
      <div class="rule"></div>
      <p class="address">12, Sunder Nagar<br>Nashik, 422001, India</p>
      <div class="rule"></div>
      <ul class="contact-list">
        <li>
          <svg viewBox="0 0 16 16" aria-hidden="true"><rect x="4" y="1" width="8" height="14" rx="1.5" fill="none" stroke="#1f9ad6" stroke-width="1.4"/></svg>
          +919800112233
        </li>
        <li>
          <svg viewBox="0 0 16 16" aria-hidden="true"><rect x="1" y="3" width="14" height="10" fill="#1f9ad6"/><path d="M1 3l7 6 7-6" fill="none" stroke="#fff" stroke-width="1.2"/></svg>
          amalvade@vexalund.com
        </li>
        <li>
          <svg viewBox="0 0 16 16" aria-hidden="true"><circle cx="8" cy="8" r="6.5" fill="none" stroke="#1f9ad6" stroke-width="1.3"/><ellipse cx="8" cy="8" rx="3" ry="6.5" fill="none" stroke="#1f9ad6" stroke-width="1.1"/><path d="M1.5 8h13M2.5 5h11M2.5 11h11" stroke="#1f9ad6" stroke-width="1"/></svg>
          www.vexalund.com
        </li>
      </ul>
      <div class="rule"></div>
      <p class="tagline-front">Care Beyond Borders</p>
    </div>
  </section>

  <section class="card card-back" aria-label="Back of card">
    <div class="back-pattern" role="img" aria-label="Repeating brand-mark pattern in coral tones"></div>
    <div class="back-brand">
      <p class="back-name">Vexalund</p>
      <div class="back-rule"></div>
      <p class="back-tagline">CARE BEYOND BORDERS</p>
    </div>
  </section>
</main>
</body>
</html>
```